Jewelers Website

This is for the DESIGN ONLY.
I am a software programmer and will be doing the development.
New website design for
www.lunacrestgems.com.au
Need a fresh new look for an online only jewellery business who produce their jewellery by hand. I would like it designed in a parallax style. Feel free to recommend fonts to use for the site. This is an Australian based company located in NSW so shots of sites in NSW might make nice background images.
http://vornaplex.me/demo/#theme=parallax
To contain the below sections
About Us
Contact Us
Gallery
Testimonials
Diamond Types
The colour scheme is to be Black / White and Silver.
With the Parallax style there will be moving sections and images for added impact.
Target Market(s)
Young Adults mainly engagement jewellery

```html
<!DOCTYPE html>
<html lang="en">
<head>
<meta charset="utf-8">
<title>Lunacrest Gems</title>
<link rel="stylesheet" href="https://fonts.googleapis.com/css2?family=Arimo:wght@400;700&family=Tinos:wght@400&family=Dancing+Script:wght@400;600&display=swap">
<style>
:root{
  --ink:#1e1e1e;
  --band:#2e2e2e;
  --band-deep:#222;
  --paper:#f7f7f7;
  --white:#fff;
  --text:#333;
  --muted:#9a9a9a;
  --line:#d9d9d9;
  --accent:#d62828;
  --silver:#c8c8c8;
  --sans:'Arimo', Arial, sans-serif;
  --serif:'Tinos', 'Times New Roman', serif;
  --script:'Dancing Script', cursive;
}
*{box-sizing:border-box;margin:0;padding:0}
html,body{width:1200px;height:3711px;overflow:hidden;background:var(--paper)}
body{font-family:var(--sans);color:var(--text)}
.page{position:relative;width:1200px;height:3711px;overflow:hidden;background:var(--paper)}
.abs{position:absolute}

/* header */
.site-header{position:absolute;left:0;top:0;width:1200px;height:106px;background:var(--ink);z-index:3}
.brand{position:absolute;left:131px;top:24px;font-family:var(--serif);color:var(--white);font-size:31px;line-height:32px;letter-spacing:1px}
.main-nav a{position:absolute;top:42px;color:var(--white);font-family:var(--serif);font-size:17px;text-decoration:none}

/* hero */
.hero{position:absolute;left:0;top:106px;width:1200px;height:640px;clip-path:polygon(0 0,100% 0,100% 91%,0 100%);
  background:linear-gradient(180deg,#2f3a52 0%,#6b6a78 28%,#d08a5a 46%,#8a5a4a 58%,#3c3840 78%,#1d1e24 100%)}
.hero-title{position:absolute;left:0;width:1200px;text-align:center;color:var(--white);font-weight:700}
.hero-title .small{display:block;font-size:46px;position:absolute;top:130px;width:100%}
.hero-title .large{display:block;font-size:64px;position:absolute;top:186px;width:100%;letter-spacing:1px}
.hero-lede{position:absolute;left:246px;top:285px;width:720px;color:var(--white);font-size:17px;line-height:31px}
.btn-ghost{position:absolute;left:510px;top:352px;width:180px;height:48px;background:rgba(120,120,120,.75);color:#eee;font-size:19px;font-weight:700;text-align:center;line-height:48px}
.hero-arrow{position:absolute;top:418px;width:40px;height:40px;border:2px solid var(--white);border-radius:50%}

/* about */
.about-label{position:absolute;left:156px;top:770px;font-family:var(--serif);color:var(--accent);font-size:25px}
.about-text{position:absolute;left:280px;top:772px;width:775px;font-size:11px;line-height:21px;color:var(--text)}
.feature{position:absolute;top:890px;width:270px;height:278px;border:1px solid #ececec;text-align:center}
.feature .icon{width:104px;height:104px;margin:22px auto 0;border-radius:50%;background:var(--ink);display:flex;align-items:center;justify-content:center}
.feature h3{font-family:var(--serif);font-weight:400;font-size:17px;color:#444;margin-top:22px}
.feature p{font-size:11px;line-height:19px;color:var(--muted);margin:10px 24px 0}

/* gallery */
.gallery-band{position:absolute;left:0;top:1222px;width:1200px;height:750px;clip-path:polygon(0 0,100% 8%,100% 92%,0 100%);
  background:linear-gradient(180deg,#2a2a2a,#3d3d3d 45%,#2c2c2c)}
.section-title{position:absolute;left:0;width:1200px;text-align:center;font-family:var(--serif);font-size:56px;font-weight:400}
.section-title::after{content:"";display:block;width:110px;height:1px;background:currentColor;margin:10px auto 0;opacity:.6}
.tagline{position:absolute;left:0;width:1200px;text-align:center;font-family:var(--script);font-size:21px}
.tile{position:absolute;width:228px;height:175px}
.tile-caption{position:absolute;inset:0;background:rgba(20,20,20,.78);color:var(--white);text-align:center}
.tile-caption h4{font-family:var(--serif);font-style:italic;font-weight:400;font-size:28px;margin-top:36px}
.tile-caption hr{width:90px;border:0;border-top:1px solid #aaa;margin:8px auto}
.tile-caption p{font-size:11px;line-height:17px;margin:0 30px}
.dots span{position:absolute;width:13px;height:13px;border-radius:50%;background:var(--white)}
.dots span.on{background:var(--accent)}

/* diamond types */
.type-card{position:absolute;top:2108px;width:265px;text-align:center}
.type-card .photo{height:143px}
.type-card .notch{width:0;height:0;margin:0 auto;border-left:14px solid transparent;border-right:14px solid transparent;border-top:14px solid #2b2b2b}
.type-card h4{font-family:var(--script);font-weight:400;font-size:18px;color:#444;margin-top:20px}
.type-card p{font-size:11px;line-height:18px;color:var(--muted);margin:8px 10px 0}
.btn-outline{display:inline-block;margin-top:14px;width:114px;height:36px;line-height:34px;border:1px solid var(--line);font-size:12px;color:#555;background:var(--white)}

/* testimonials */
.testimonial-band{position:absolute;left:0;top:2412px;width:1200px;height:520px;clip-path:polygon(0 0,100% 6%,100% 100%,0 100%);
  background:linear-gradient(180deg,#262626,#474747 50%,#2f2f2f)}
.quote-text{position:absolute;left:158px;top:2640px;width:884px;text-align:center;color:var(--white);font-size:12px;line-height:24px}
.quote-mark{position:absolute;color:var(--white);font-family:var(--serif);font-size:64px;font-weight:700;line-height:1}
.avatar{position:absolute;left:556px;top:2728px;width:100px;height:100px;border-radius:50%;border:3px solid var(--white);background:radial-gradient(circle at 50% 40%,#c9a48a,#6b5446)}
.reviewer{position:absolute;left:0;width:1200px;text-align:center;color:var(--white)}

/* map */
.map{position:absolute;left:0;top:2870px;width:1200px;height:350px;clip-path:polygon(0 18%,100% 0,100% 100%,0 100%);
  background:linear-gradient(135deg,#d6d6d6,#e4e4e4 50%,#cfcfcf)}

/* contact */
.field{position:absolute;height:38px;border:1px solid var(--line);background:var(--white);font-size:11px;color:#aaa;padding:10px 12px}
.btn-dark{position:absolute;left:584px;top:3384px;width:178px;height:38px;background:var(--ink);color:var(--white);font-size:14px;text-align:center;line-height:38px;letter-spacing:1px}

/* footer */
.site-footer{position:absolute;left:0;top:3458px;width:1200px;height:253px;clip-path:polygon(0 0,100% 12%,100% 100%,0 100%);
  background:linear-gradient(180deg,#2a2a2a,#3a3a3a 60%,#202020)}
.social span{position:absolute;top:3555px;width:54px;height:54px;border-radius:50%;background:var(--white)}
.copyright{position:absolute;left:0;top:3640px;width:1200px;text-align:center;color:var(--white);font-family:var(--serif);font-size:13px}
</style>
</head>
<body>
<div class="page">

  <header class="site-header">
    <div class="brand">LUNACREST<br>GEMS</div>
    <nav class="main-nav">
      <a style="left:360px">Home</a>
      <a style="left:457px">About Us</a>
      <a style="left:574px">Contact Us</a>
      <a style="left:705px">Gallery</a>
      <a style="left:810px">Testimonials</a>
      <a style="left:956px">Diamond Types</a>
    </nav>
  </header>

  <section class="hero" role="img" aria-label="Sunset over a coastal ocean pool beside cliffs">
    <h1 class="hero-title"><span class="small">WELCOME TO</span><span class="large">LUNACREST GEMS</span></h1>
    <p class="hero-lede">Because we operate solely over the Internet, we are able to focus all our efforts on product that no matter where you are located in the country.</p>
    <div class="btn-ghost">READ MORE</div>
    <span class="hero-arrow" style="left:554px"><svg width="36" height="36" viewBox="0 0 36 36"><path d="M21 10l-8 8 8 8" fill="none" stroke="#fff" stroke-width="2.5"/></svg></span>
    <span class="hero-arrow" style="left:604px"><svg width="36" height="36" viewBox="0 0 36 36"><path d="M15 10l8 8-8 8" fill="none" stroke="#fff" stroke-width="2.5"/></svg></span>
  </section>

  <section class="about">
    <h2 class="about-label">About Us :</h2>
    <p class="about-text">We specialise in the design and creation of one-off pieces of exceptional quality that cannot be found elsewhere. Our team of highly skilled jewellers based in Sydney are committed to making sure that each ring we produce is unique and only the finest materials are used so you can be sure that whatever you order will be truly special. Many Internet jewellery stores stock affordable pieces and a select few offers items of breathtaking beauty. However, few are capable of offering both.</p>

    <div class="feature" style="left:140px">
      <div class="icon"><svg width="52" height="52" viewBox="0 0 52 52" fill="#fff"><rect x="6" y="18" width="40" height="10"/><rect x="9" y="30" width="34" height="18"/><rect x="23" y="18" width="6" height="30" fill="#1e1e1e"/><path d="M26 18c-4-10-16-10-12-2 2 3 8 2 12 2zm0 0c4-10 16-10 12-2-2 3-8 2-12 2z"/></svg></div>
      <h3>Diamond Engagement Rings</h3>
      <p>We specialise in the design and creation of one-off pieces of exceptional quality that cannot be elsewhere Our team.</p>
    </div>
    <div class="feature" style="left:464px">
      <div class="icon"><svg width="56" height="56" viewBox="0 0 56 56" fill="#fff"><circle cx="28" cy="28" r="5"/><path d="M28 20L20 6a26 26 0 0 1 16 0z"/><path d="M35 32l16 0a26 26 0 0 1-8 14z"/><path d="M21 32L13 46a26 26 0 0 1-8-14z"/></svg></div>
      <h3>Diamond Engagement Rings</h3>
      <p>We specialise in the design and creation of one-off pieces of exceptional quality that cannot be elsewhere Our team.</p>
    </div>
    <div class="feature" style="left:788px">
      <div class="icon"><svg width="56" height="56" viewBox="0 0 56 56" fill="#fff"><circle cx="28" cy="8" r="5"/><circle cx="28" cy="32" r="20"/><path d="M28 20l3.5 7.5 8 .8-6 5.4 1.8 8L28 37.6 20.7 41.7l1.8-8-6-5.4 8-.8z" fill="#1e1e1e"/></svg></div>
      <h3>Diamond Engagement Rings</h3>
      <p>We specialise in the design and creation of one-off pieces of exceptional quality that cannot be elsewhere Our team.</p>
    </div>
  </section>

  <section class="gallery-band" role="img" aria-label="Blurred city skyline behind the gallery"></section>
  <h2 class="section-title" style="top:1296px;color:#fff">Our Gallery</h2>
  <p class="tagline" style="top:1398px;color:#fff">Contrary to popular belief, Lorem Ipsum is not simply random text. It has roots in piece of classical Latin literature from BC, it is old.</p>

  <div class="gallery-grid">
    <div class="tile" role="img" aria-label="Loose diamonds on dark cloth" style="left:131px;top:1465px;background:linear-gradient(135deg,#555,#ccc 45%,#333)"></div>
    <div class="tile" role="img" aria-label="Diamonds on black" style="left:367px;top:1465px;background:linear-gradient(135deg,#444,#999 50%,#222)">
      <div class="tile-caption"><h4>Diamond</h4><hr><p>Because we operate solely over the efforts on producing.</p></div>
    </div>
    <div class="tile" role="img" aria-label="Single diamond on grey" style="left:603px;top:1465px;background:linear-gradient(135deg,#888,#eee 50%,#777)"></div>
    <div class="tile" role="img" aria-label="Diamond ring close-up" style="left:839px;top:1465px;background:linear-gradient(135deg,#222,#bbb 50%,#444)"></div>
    <div class="tile" role="img" aria-label="Solitaire ring on dark surface" style="left:131px;top:1651px;background:linear-gradient(135deg,#2a2a2a,#888 50%,#444)"></div>
    <div class="tile" role="img" aria-label="Scattered diamonds on black" style="left:367px;top:1651px;background:linear-gradient(135deg,#111,#777 50%,#111)"></div>
    <div class="tile" role="img" aria-label="Pear cut diamond" style="left:603px;top:1651px;background:linear-gradient(135deg,#333,#aaa 50%,#2a2a2a)"></div>
    <div class="tile" role="img" aria-label="Falling diamonds on black" style="left:839px;top:1651px;background:linear-gradient(135deg,#0c0c0c,#666 50%,#111)"></div>
  </div>
  <div class="dots"><span style="left:583px;top:1874px"></span><span class="on" style="left:600px;top:1874px"></span><span style="left:617px;top:1874px"></span></div>

  <section class="diamond-types">
    <h2 class="section-title" style="top:1958px;color:#222;font-size:48px">Diamond Types</h2>
    <p class="tagline" style="top:2042px;color:#333">Contrary to popular belief, Lorem Ipsum is not simply random text. It has roots in piece of classical Latin literature from BC, it is old.</p>
    <div class="type-card" style="left:166px">
      <div class="photo" role="img" aria-label="Loose diamonds" style="background:linear-gradient(135deg,#333,#ccc 50%,#444)"></div>
      <div class="notch"></div>
      <h4>Diamond engagement rings</h4>
      <p>We specialise in the design and creation of one-off pieces of exceptional quality that cannot</p>
      <span class="btn-outline">READ MORE</span>
    </div>
    <div class="type-card" style="left:470px">
      <div class="photo" role="img" aria-label="Heart cut diamond" style="background:linear-gradient(135deg,#777,#eee 50%,#888)"></div>
      <div class="notch"></div>
      <h4>Diamond engagement rings</h4>
      <p>We specialise in the design and creation of one-off pieces of exceptional quality that cannot</p>
      <span class="btn-outline">READ MORE</span>
    </div>
    <div class="type-card" style="left:774px">
      <div class="photo" role="img" aria-label="Diamonds falling on black" style="background:linear-gradient(135deg,#0e0e0e,#666 50%,#111)"></div>
      <div class="notch"></div>
      <h4>Diamond engagement rings</h4>
      <p>We specialise in the design and creation of one-off pieces of exceptional quality that cannot</p>
      <span class="btn-outline">READ MORE</span>
    </div>
  </section>

  <section class="testimonial-band" role="img" aria-label="Blurred city street behind testimonials"></section>
  <h2 class="section-title" style="top:2528px;color:#fff;font-size:46px">Testimonials</h2>
  <span class="quote-mark" style="left:140px;top:2590px">&ldquo;</span>
  <p class="quote-text">Lorem ipsum dolor sit amet, consectetur adipisicing elit, sed do eiusmod tempor incididunt ut labore et dolore magna aliqua. Ut enim ad minim veniam, quis nostrud exercitation ullamco laboris nisi ut aliquip ex ea commodo consequat. Duis aute irure dolor in reprehenderit in voluptate velit esse cillum dolore eu fugiat nulla pariatur. consectetur commodo consequat. Duis aute irure dolor in reprehenderit in voluptate velit esse cillum dolore eu fugiat nulla pariatur.</p>
  <span class="quote-mark" style="left:918px;top:2712px">&rdquo;</span>
  <svg class="abs" style="left:444px;top:2752px" width="28" height="52" viewBox="0 0 28 52"><path d="M24 2L4 26l20 24" fill="none" stroke="#fff" stroke-width="3"/></svg>
  <svg class="abs" style="left:762px;top:2752px" width="28" height="52" viewBox="0 0 28 52"><path d="M4 2l20 24L4 50" fill="none" stroke="#fff" stroke-width="3"/></svg>
  <div class="avatar" role="img" aria-label="Customer portrait"></div>
  <p class="reviewer" style="top:2838px;font-size:17px">MARLA QUINN</p>
  <p class="reviewer" style="top:2862px;font-size:11px;color:#ccc">on 25 Apr 2014</p>
  <div class="dots"><span style="left:583px;top:2882px"></span><span class="on" style="left:600px;top:2882px"></span><span style="left:617px;top:2882px"></span></div>

  <div class="map" role="img" aria-label="Street map of the store area"></div>

  <form class="contact-form">
    <div class="field" style="left:193px;top:3265px;width:369px">Name</div>
    <div class="field" style="left:193px;top:3325px;width:369px">Email</div>
    <div class="field" style="left:193px;top:3384px;width:369px">Phone</div>
    <div class="field" style="left:584px;top:3265px;width:463px;height:96px">Messages</div>
    <div class="btn-dark">SUBSCRIBE</div>
  </form>

  <footer class="site-footer" role="img" aria-label="Blurred city backdrop"></footer>
  <div class="social">
    <span style="left:393px"></span><span style="left:453px"></span><span style="left:513px"></span><span style="left:572px"></span><span style="left:631px"></span><span style="left:690px"></span><span style="left:752px"></span>
  </div>
  <p class="copyright">Copy Rights 2014 Lunacrest Gems.All Rights Reserved.</p>

</div>
</body>
</html>
```